Stretch on the Green with Mira

I want to advertise my Stretch on the Green classes for Summer. Classes are outside at the lovely local park. Tolmore field. 12 Rawhiti St. Kowhai Heights.
Classes are for beginners to advance levels.
Classes start Monday, October 17th.
Monday 6pm Beginners
Tuesday 6pm Intermediate
Thursday 6pm Intermediate/Advance
Saturday 9am All fitness levels
My Pilates classes are specially designed to help improve strength and flexibility but as well will also improve posture, reduce stress and develop control and endurance in the entire body.
Booking essential. Limited numbers so I can make sure the correct technique is always being followed.
For more info or to book contact details:
Mira 027385116
mira@stretchwithmira.net
www.stretchwithmira.net
$15 Per Session

Target Market(s)

Males and Females ages 35plus.

Industry/Entity Type

Fitness

Font styles to use
Sans Serif

Requirements
Must have
• My logo. Contact details. A Park that looks lovely to exercise at.
Nice to have
• Summer looking. Trees - inspiration to be exercising outside

```html
<!DOCTYPE html>
<html lang="en">
<head>
<meta charset="utf-8">
<title>Stretch on the Green with Mira</title>
<link rel="stylesheet" href="https://fonts.googleapis.com/css2?family=Anton&family=Montserrat:ital,wght@0,400;0,600;0,700;1,600&display=swap">
<style>
:root{
  --stage:#ffffff;
  --charcoal:#4a4a4c;
  --pink:#f386c0;
  --pink-deep:#ec6aae;
  --green:#0f6a4f;
  --ink:#1d1412;
  --grey-text:#5a5a5a;
  --mira-grey:#7b7b7b;
  --blush:#f4e5dd;
  --tab-grey:#8b8b8d;
  --white:#ffffff;
}
*{margin:0;padding:0;box-sizing:border-box}
html,body{width:1200px;height:2602px;overflow:hidden;background:var(--stage)}
.stage{position:relative;width:1200px;height:2602px}
.flyer{position:absolute;left:50px;top:588px;width:824px;height:1068px;transform:scale(1.335);transform-origin:0 0;background:var(--white);overflow:hidden;box-shadow:0 4px 14px rgba(0,0,0,.18);font-family:'Montserrat',sans-serif;color:var(--ink)}
.backdrop{position:absolute;left:0;top:0;width:824px;height:1068px}
.abs{position:absolute}
.brand{left:0;width:420px;top:86px;text-align:center;font-family:'Montserrat',sans-serif;font-weight:400;font-size:16px;letter-spacing:2px;text-transform:uppercase;color:var(--pink)}
.brand-dot{left:201px;top:42px;width:18px;height:18px;border-radius:50%;background:var(--pink)}
.price{left:68px;top:298px;width:160px;height:160px;border-radius:50%;background:var(--white);padding:4px}
.price-inner{width:100%;height:100%;border-radius:50%;background:var(--blush);border:3px solid var(--pink);text-align:center;font-family:'Anton',sans-serif;line-height:1}
.price-amount{display:block;font-size:50px;color:var(--green);padding-top:22px}
.price-label{display:block;font-size:22px;color:var(--ink);margin-top:4px;line-height:1.05}
.title{left:34px;top:478px;font-family:'Anton',sans-serif;font-weight:400;font-size:44px;line-height:1.02;letter-spacing:.5px;text-transform:uppercase;color:var(--ink)}
.title .name{color:var(--mira-grey)}
.venue{left:34px;top:572px;height:22px;padding:0 8px;background:var(--green);color:var(--white);font-family:'Anton',sans-serif;font-size:15px;line-height:22px;letter-spacing:.5px}
.schedule{left:34px;top:622px;width:440px;height:90px}
.slot{position:absolute;padding-left:20px}
.slot::before{content:"";position:absolute;left:0;top:4px;width:11px;height:11px;border-radius:50%;background:var(--pink)}
.slot::after{content:"";position:absolute;left:3px;top:7px;width:4px;height:2px;border-left:1.5px solid var(--white);border-bottom:1.5px solid var(--white);transform:rotate(-45deg)}
.slot b{display:block;font-size:15px;font-weight:700;line-height:1.1}
.slot span{display:block;font-size:11px;font-weight:600;line-height:1.3}
.divider{position:absolute;left:174px;top:4px;width:1px;height:76px;background:#cfcfcf}
.start{left:520px;top:596px}
.start-head{font-family:'Anton',sans-serif;font-size:33px;line-height:1;color:var(--ink)}
.start-date{margin-top:4px;display:inline-block;background:var(--pink);color:var(--white);font-family:'Anton',sans-serif;font-size:18px;line-height:24px;padding:0 7px;letter-spacing:.5px}
.circle-photo{width:124px;height:124px;border-radius:50%;border:3px solid var(--pink);padding:4px;background:var(--white)}
.circle-photo div{width:100%;height:100%;border-radius:50%}
.cp-one{left:518px;top:452px}
.cp-one div{background:linear-gradient(160deg,#cfe0ec 0%,#9fb6c9 45%,#5b4c58 100%)}
.cp-two{left:661px;top:452px}
.cp-two div{background:linear-gradient(170deg,#eef1f4 0%,#b9b6b2 45%,#2e2b2e 100%)}
.photo{border:2px solid #e7c9d6}
.photo-bridge{left:35px;top:730px;width:250px;height:95px;background:linear-gradient(180deg,#6a5448 0%,#3b3331 55%,#7f7a78 100%)}
.about{left:311px;top:736px;width:480px;font-size:14.2px;line-height:1.38;color:var(--grey-text)}
.about em{font-style:normal;color:var(--pink-deep)}
.cal{left:35px;top:848px;width:54px;height:54px}
.booking{left:102px;top:852px;font-family:'Anton',sans-serif;font-size:28px;line-height:1.02;letter-spacing:.5px}
.booking-rule{left:275px;top:850px;width:1px;height:56px;background:#cfcfcf}
.limited{left:297px;top:850px}
.limited h3{font-family:'Anton',sans-serif;font-weight:400;font-size:22px;line-height:1.1;color:var(--green);letter-spacing:.5px}
.limited p{font-size:11.4px;line-height:1.3;color:var(--grey-text)}
.photo-cobra{left:537px;top:818px;width:249px;height:93px;background:linear-gradient(180deg,#9cc4dc 0%,#c9d7d7 30%,#7aa34b 55%,#5c8a34 100%)}
.info-tab{left:0;top:925px;width:402px;height:37px;background:var(--tab-grey);color:var(--white);font-size:15.5px;line-height:37px;padding-left:34px}
.info-tab i{font-weight:600}
.phone-row{left:142px;top:978px;display:flex;align-items:center;gap:6px;font-size:18px;font-weight:600}
.phone-icon{width:22px;height:22px}
.web-row{left:142px;top:1008px;display:flex;align-items:center;gap:6px;font-size:11.5px;font-weight:600}
.web-row .sep{width:1px;height:14px;background:#b8a8a0;margin:0 6px}
.mini{width:14px;height:14px}
</style>
</head>
<body>
<div class="stage">
  <main class="flyer">
    <svg class="backdrop" viewBox="0 0 824 1068" xmlns="http://www.w3.org/2000/svg">
      <defs>
        <linearGradient id="parkTones" x1="0" y1="0" x2="1" y2="1">
          <stop offset="0" stop-color="#8aa64a"/>
          <stop offset=".45" stop-color="#6f8f3a"/>
          <stop offset=".8" stop-color="#a6b35e"/>
          <stop offset="1" stop-color="#4e5a2c"/>
        </linearGradient>
        <linearGradient id="shoreTones" x1="0" y1="0" x2="1" y2="0">
          <stop offset="0" stop-color="#9fb8c8"/>
          <stop offset=".7" stop-color="#d8cfc2"/>
          <stop offset="1" stop-color="#f4e5dd"/>
        </linearGradient>
        <linearGradient id="lawnTones" x1="0" y1="0" x2="0" y2="1">
          <stop offset="0" stop-color="#a9c08a"/>
          <stop offset=".5" stop-color="#7fa048"/>
          <stop offset="1" stop-color="#5f8a30"/>
        </linearGradient>
      </defs>
      <path role="img" aria-label="Photo: group class stretching on mats in a sunny park" d="M0 0H824V452L0 370Z" fill="url(#parkTones)"/>
      <path d="M0 0H760L205 185L0 95Z" fill="var(--charcoal)"/>
      <path d="M0 95L205 185L760 0H800L205 200L0 104Z" fill="var(--pink)"/>
      <path d="M0 370L824 452V545L0 472Z" fill="var(--pink)"/>
      <path d="M0 472L824 545V1068H0Z" fill="var(--white)"/>
      <path d="M506 545V685H783" fill="none" stroke="var(--pink)" stroke-width="2"/>
      <circle cx="783" cy="685" r="4" fill="var(--pink)"/>
      <rect x="0" y="925" width="824" height="143" fill="var(--blush)"/>
      <path role="img" aria-label="Photo: person stretching on a jetty by the water" d="M0 985H157V1068H0Z" fill="url(#shoreTones)"/>
      <path d="M548 943H780L785 1035H555Z" fill="var(--white)" stroke="var(--pink)" stroke-width="2"/>
      <path role="img" aria-label="Photo: women doing plank poses on the lawn" d="M552 947H776L781 1031H559Z" fill="url(#lawnTones)"/>
    </svg>

    <div class="abs brand-dot"></div>
    <div class="abs brand">Stretch with Mira</div>

    <div class="abs price"><div class="price-inner"><span class="price-amount">$15</span><span class="price-label">PER<br>SESSION</span></div></div>

    <div class="abs circle-photo cp-one"><div role="img" aria-label="Photo: seated forward fold on a mat"></div></div>
    <div class="abs circle-photo cp-two"><div role="img" aria-label="Photo: class doing a side stretch together"></div></div>

    <h1 class="abs title">Stretch on the Green<br>with <span class="name">Mira</span></h1>
    <div class="abs venue">TOLMORE FIELD. 12 RAWHITI ST. KOWHAI HEIGHTS</div>

    <section class="abs schedule">
      <div class="slot" style="left:0;top:0"><b>BEGINNERS</b><span>MONDAY 6PM</span></div>
      <div class="slot" style="left:0;top:46px"><b>INTERMEDIATE</b><span>TUESDAY 6PM</span></div>
      <div class="divider"></div>
      <div class="slot" style="left:194px;top:0"><b>INTERMEDIATE | ADVANCE</b><span>THURSDAY 6PM</span></div>
      <div class="slot" style="left:194px;top:46px"><b>ALL FITNESS LEVELS</b><span>SATURDAY 9AM</span></div>
    </section>

    <section class="abs start">
      <div class="start-head">CLASSES START</div>
      <div class="start-date">MONDAY | OCTOBER 17TH</div>
    </section>

    <div class="abs photo photo-bridge" role="img" aria-label="Photo: woman in a bridge pose on a mat indoors"></div>
    <p class="abs about">My Pilates classes are specially designed to help improve <em>strength and flexibility</em> but as well will also improve posture, <em>reduce stress and develop control</em> and endurance in the entire body.</p>

    <svg class="abs cal" viewBox="0 0 54 54" xmlns="http://www.w3.org/2000/svg" fill="none" stroke="var(--pink)" stroke-width="2">
      <rect x="2" y="7" width="50" height="44" rx="3"/>
      <line x1="2" y1="17" x2="52" y2="17"/>
      <line x1="14" y1="2" x2="14" y2="11"/><line x1="40" y1="2" x2="40" y2="11"/>
      <rect x="8" y="23" width="10" height="9"/><rect x="22" y="23" width="10" height="9"/><rect x="36" y="23" width="10" height="9"/>
      <rect x="8" y="36" width="10" height="9"/><rect x="22" y="36" width="10" height="9"/><rect x="36" y="36" width="10" height="9"/>
      <path d="M38 40l3 3 4-5"/>
    </svg>
    <div class="abs booking">BOOKING<br>ESSENTIAL</div>
    <div class="abs booking-rule"></div>
    <div class="abs limited"><h3>LIMITED NUMBERS</h3><p>So I can make sure the correct<br>technique is always being followed.</p></div>

    <div class="abs photo photo-cobra" role="img" aria-label="Photo: woman in a cobra stretch on grass by the sea"></div>

    <div class="abs info-tab">For more info or to <i>book contact details:</i></div>

    <div class="abs phone-row">
      <svg class="phone-icon" viewBox="0 0 22 22" xmlns="http://www.w3.org/2000/svg"><circle cx="11" cy="11" r="10" fill="var(--charcoal)"/><path d="M7.5 6h2l1 3-1.3 1c.6 1.3 1.5 2.2 2.8 2.8l1-1.3 3 1v2c0 .6-.5 1-1 1-4.5-.3-8.2-4-8.5-8.5 0-.5.4-1 1-1z" fill="var(--white)"/></svg>
      <span>Mira 027385116</span>
    </div>
    <div class="abs web-row">
      <svg class="mini" viewBox="0 0 14 14" xmlns="http://www.w3.org/2000/svg"><rect x="1" y="3" width="12" height="8" fill="var(--pink)"/><path d="M1 3l6 5 6-5" fill="none" stroke="var(--white)" stroke-width="1"/></svg>
      <span>mira@stretchwithmira.net</span>
      <span class="sep"></span>
      <svg class="mini" viewBox="0 0 14 14" xmlns="http://www.w3.org/2000/svg" fill="none" stroke="var(--pink)" stroke-width="1.2"><circle cx="7" cy="7" r="6"/><ellipse cx="7" cy="7" rx="2.6" ry="6"/><line x1="1" y1="7" x2="13" y2="7"/></svg>
      <span>www.stretchwithmira.net</span>
    </div>
  </main>
</div>
</body>
</html>
```